Kestrel Finish Studio (KFS)

I would like to design a dedicated site for my KFS product, which allows industry employees to be trained in the visual inspection of mechanical parts. My product is a 3D simulator (see https://morvint-works.ch/our-applications/virtual-reality/ and https://morvint-works.ch for videos) which makes it possible to manufacture standard parts representative of a type of defect which is accepted or refused by the quality department. These master parts can be used to create a common quality culture in the company and to train employees in a homogeneous way. The simulator is initially designed for watchmaking, but must be designed for much broader industries (cars, phone reconditioning, ball bearings, etc.)
L'information que j'ai donnée n'est pas assez précise. Je dois préciser les domaines métiers visés par le site internet. J'ai besoin de quelques jours pour choisir les domaines les plus représentatifs.
Coded - Design and coding required
1 page

```html
<!DOCTYPE html>
<html lang="en">
<head>
<meta charset="utf-8">
<title>Kestrel Finish Studio</title>
<link href="https://fonts.googleapis.com/css2?family=Montserrat:wght@600;700&family=Roboto:wght@300;400;500&display=swap" rel="stylesheet">
<style>
:root{
  --blue:#0a72c4;
  --blue-deep:#0758a8;
  --navy:#1c2233;
  --ink:#1e2230;
  --text:#555b66;
  --grey-bg:#f2f2f2;
  --white:#ffffff;
}
*{margin:0;padding:0;box-sizing:border-box}
html,body{width:1200px;height:5038px;overflow:hidden;background:var(--white)}
body{font-family:'Roboto',sans-serif;color:var(--text);position:relative}
.section{position:absolute;left:0;width:1200px}
.heading{font-family:'Montserrat',sans-serif;font-weight:700;color:var(--ink);font-size:38px;line-height:43px;text-align:center;text-transform:uppercase;letter-spacing:.3px}
.heading.light{color:var(--white)}
.marker{width:0;height:0;border-left:12px solid transparent;border-right:12px solid transparent;border-top:22px solid var(--blue);margin:12px auto 0}
.marker.light{border-top-color:var(--white)}
.photo{position:absolute}
.band-bg{position:absolute;left:0;top:0}

/* hero */
.hero{top:0;height:755px}
.hero-photo{position:absolute;left:0;top:0;width:1200px;height:755px;background:radial-gradient(ellipse at 70% 50%,#6b6254 0%,#3a3733 40%,#151515 90%)}
.brand{position:absolute;left:112px;top:28px;font-family:'Montserrat',sans-serif;font-weight:700;color:var(--white);font-size:21px;line-height:30px;text-transform:uppercase}
.nav{position:absolute;left:536px;top:48px;display:flex;gap:0}
.nav a{font-family:'Roboto',sans-serif;font-weight:500;font-size:14px;color:var(--white);text-decoration:none;margin-right:34px;padding-bottom:5px}
.nav a.active{border-bottom:2px solid var(--white)}
.login{position:absolute;left:1030px;top:48px;font-weight:500;font-size:14px;color:var(--white)}
.hero-box{position:absolute;left:112px;top:264px;width:496px;height:204px;background:rgba(20,20,20,.78);padding:12px 0 0 0}
.hero-box h1{font-family:'Montserrat',sans-serif;font-weight:700;color:var(--white);font-size:42px;line-height:52px;text-transform:uppercase}
.hero-box p{font-family:'Montserrat',sans-serif;font-weight:700;color:var(--white);font-size:14px;line-height:25px;margin-top:10px;text-transform:uppercase}

/* control */
.control{top:800px;height:560px}
.check-list{position:absolute;left:112px;top:140px;width:470px;list-style:none}
.check-list li{position:relative;padding-left:26px;font-size:14px;line-height:21px;margin-bottom:21px}
.check-list li::before{content:"";position:absolute;left:0;top:4px;border-top:7px solid transparent;border-bottom:7px solid transparent;border-left:13px solid var(--blue)}
.btn{position:absolute;left:112px;top:403px;width:144px;height:42px;background:var(--blue);color:var(--white);font-weight:500;font-size:14px;line-height:42px;text-align:center;text-transform:uppercase}
.offset{position:absolute;background:var(--blue)}

/* band text */
.band-copy{position:absolute;font-size:14px;line-height:26px;color:#e8f1fb;text-align:center}
.body-copy{position:absolute;font-size:14px;line-height:25.5px;text-align:justify}

/* allows */
.features{position:absolute;top:170px;left:112px;width:976px;display:flex}
.feature{width:244px;text-align:center}
.feature p{font-size:14px;line-height:24px;margin:20px auto 0;width:210px}

/* footer */
.footer{top:4680px;height:358px}
.footer h4{font-family:'Montserrat',sans-serif;font-weight:700;font-size:14px;color:var(--ink);text-transform:uppercase}
.footer .brand-f{font-family:'Montserrat',sans-serif;font-weight:700;color:var(--ink);font-size:21px;line-height:30px;text-transform:uppercase}
.fcol{position:absolute;top:20px}
.fcol p,.fcol a{font-size:12.5px;line-height:21px;color:var(--text);text-decoration:none;display:block}
.links a{margin-bottom:13px}
.contact-row{display:flex;align-items:flex-start;margin-top:16px}
.contact-row svg{flex:none;margin-right:10px;margin-top:4px}
.divider{position:absolute;left:100px;top:4976px;width:1000px;height:1px;background:#e3e3e3}
.copyright{position:absolute;top:5002px;left:0;width:1200px;text-align:center;font-size:12px;color:var(--text)}
</style>
</head>
<body>

<!-- hero -->
<header class="section hero">
  <div class="hero-photo" role="img" aria-label="Close-up of a watchmaker's hands assembling a mechanical movement with gears and tools"></div>
  <div class="brand">Kestrel Finish<br>Studio</div>
  <nav class="nav">
    <a class="active">HOME</a><a>ABOUT US</a><a>SERVICES</a><a>BLOG</a><a>CONTACT US</a>
  </nav>
  <div class="login">&#9679; LOGIN</div>
  <div class="hero-box">
    <h1>Kestrel Finish<br>Studio</h1>
    <p>Virtual reality at the service of controlled<br>aesthetic watchmaking</p>
  </div>
  <svg class="band-bg" width="1200" height="755" viewBox="0 0 1200 755">
    <polygon points="640,690 1200,628 1200,755 0,755 0,755" fill="var(--blue)"/>
    <polygon points="0,755 640,690 1200,755" fill="var(--white)"/>
    <polygon points="560,680 600,652 640,680 640,712 560,712" fill="var(--white)"/>
    <polyline points="593,686 600,693 607,686" fill="none" stroke="var(--ink)" stroke-width="1.6"/>
    <polyline points="593,692 600,699 607,692" fill="none" stroke="var(--ink)" stroke-width="1.6"/>
  </svg>
</header>

<!-- how to control -->
<section class="section control">
  <h2 class="heading" style="margin-top:15px">How to control it?</h2>
  <div class="marker"></div>
  <ul class="check-list">
    <li>Adopting a simple and unambiguous language for a common understanding of aesthetic quality at the extended enterprise level.</li>
    <li>By using a semantic reference matrix associating the types of anomalies (scratches, marks, deformations, stains, etc.) with the intensity levels defined with the company.</li>
    <li>Determining the compliance thresholds of the component or product.</li>
    <li>Providing uniform training in operational competence for those responsible for aesthetic control.</li>
  </ul>
  <div class="btn">Learn more</div>
  <div class="offset" style="left:1000px;top:333px;width:87px;height:125px"></div>
  <div class="photo" style="left:617px;top:147px;width:455px;height:293px;background:linear-gradient(135deg,#8a5a6e 0%,#cfd3dc 45%,#6b7488 100%)" role="img" aria-label="Technician inspecting a mechanical part under an inspection station screen"></div>
</section>

<!-- lighten band -->
<section class="section" style="top:1360px;height:625px">
  <svg class="band-bg" width="1200" height="625" viewBox="0 0 1200 625">
    <defs><linearGradient id="g1" x1="0" y1="0" x2="1" y2="1"><stop offset="0" stop-color="#0a72c4"/><stop offset="1" stop-color="#0b5fae"/></linearGradient></defs>
    <rect width="1200" height="625" fill="url(#g1)"/>
    <polygon points="0,0 420,0 0,130" fill="var(--navy)"/>
    <polygon points="1200,500 1200,625 0,625" fill="var(--navy)"/>
  </svg>
  <div role="img" aria-label="Decorative flowing dot wave" style="position:absolute;left:0;top:300px;width:1200px;height:260px;background:radial-gradient(ellipse at 60% 70%,rgba(120,190,255,.35),transparent 60%)"></div>
  <h2 class="heading light" style="position:absolute;top:168px;width:1200px">Lighten the management of<br>physical components</h2>
  <div class="marker light" style="position:absolute;top:263px;left:588px;margin:0"></div>
  <p class="band-copy" style="left:200px;top:300px;width:800px">Companies must manage and maintain sets of physical components used as a "yardstick" for the training of aesthetic testers. The cost of managing a set of physical parts representing all combinations of shapes, defect types, materials and finishes is very high.</p>
  <p class="band-copy" style="left:200px;top:404px;width:800px">KFS allows the company to significantly reduce its management burden by scanning components or products in 3D and then virtually adding 'typical' aesthetic anomalies.</p>
</section>

<!-- after-sales -->
<section class="section" style="top:1985px;height:610px">
  <h2 class="heading" style="margin-top:50px">Improve after-sales<br>service returns</h2>
  <div class="marker"></div>
  <div class="offset" style="left:122px;top:200px;width:138px;height:293px"></div>
  <div class="photo" style="left:135px;top:195px;width:122px;height:290px;background:linear-gradient(180deg,#16324f,#1e4468)" role="img" aria-label="Simulator settings panel with sliders and toggles"></div>
  <div class="photo" style="left:263px;top:195px;width:330px;height:298px;background:radial-gradient(ellipse at 55% 50%,#a07428 0%,#3a2a10 45%,#050505 80%)" role="img" aria-label="3D render of a golden watch ring on a black background"></div>
  <p class="body-copy" style="left:628px;top:195px;width:447px">The KFS platform can easily be used by the service network staff to assist them in the objective assessment of aesthetic defects by referring to the semantic matrix as well as to the cases already referenced.</p>
  <p class="body-copy" style="left:628px;top:297px;width:447px">It is also possible, in an intuitive and playful way, to indicate, in accordance with the product nomenclature, a type of imperfection, its intensity and its location. It is also possible to draw up a precise repair estimate or to declare a non-conformity on a product coming from a market return.</p>
</section>

<!-- simulator band -->
<section class="section" style="top:2595px;height:565px">
  <svg class="band-bg" width="1200" height="565" viewBox="0 0 1200 565">
    <defs><linearGradient id="g2" x1="0" y1="0" x2="1" y2="1"><stop offset="0" stop-color="#0b6cbf"/><stop offset="1" stop-color="#0a5aa8"/></linearGradient></defs>
    <polygon points="0,0 1200,90 1200,565 0,565" fill="url(#g2)"/>
    <polygon points="0,440 1200,520 1200,565 0,565" fill="var(--navy)"/>
  </svg>
  <div role="img" aria-label="Decorative flowing dot wave" style="position:absolute;left:500px;top:200px;width:700px;height:300px;background:radial-gradient(ellipse at 65% 60%,rgba(140,200,255,.35),transparent 65%)"></div>
  <p class="body-copy" style="left:110px;top:165px;width:475px;color:var(--white);font-size:13.5px">Morvint Lab a développé en collaboration avec l'école d'horlogerie de Valmont un simulateur de défaut sur pièce mécanique. Celui-ci permet aux enseignants de former les élèves de manière plus approfondie au métier de contrôleur qualité. Cet outil combiné avec un LMS (Learning Management System) ou l'interface de gestion intégrée permet d'animer une formation de contrôle esthétique de manière ludique et efficace. Voilà la brochure du produit en attendant le site dédié.</p>
  <h2 class="heading light" style="position:absolute;left:600px;top:240px;width:488px;text-align:right">Kestrel Finish<br>Studio</h2>
  <div class="marker light" style="position:absolute;left:1064px;top:335px;margin:0"></div>
</section>

<!-- allows -->
<section class="section" style="top:3160px;height:480px">
  <h2 class="heading" style="margin-top:42px">KFS allows</h2>
  <div class="marker"></div>
  <div class="features">
    <div class="feature">
      <svg width="88" height="96" viewBox="0 0 88 96"><polygon points="44,2 86,26 86,70 44,94 2,70 2,26" fill="var(--blue)"/><circle cx="44" cy="46" r="16" fill="none" stroke="#fff" stroke-width="3"/><circle cx="44" cy="46" r="6" fill="#fff"/></svg>
      <p>Remove the management of components used as standards for aesthetic control training</p>
    </div>
    <div class="feature">
      <svg width="88" height="96" viewBox="0 0 88 96"><polygon points="44,2 86,26 86,70 44,94 2,70 2,26" fill="var(--blue)"/><circle cx="44" cy="36" r="7" fill="#fff"/><circle cx="28" cy="44" r="5" fill="#fff"/><circle cx="60" cy="44" r="5" fill="#fff"/><rect x="22" y="54" width="44" height="12" rx="4" fill="#fff"/></svg>
      <p>To make employees aware of aesthetic control and the vocabulary to be used</p>
    </div>
    <div class="feature">
      <svg width="88" height="96" viewBox="0 0 88 96"><polygon points="44,2 86,26 86,70 44,94 2,70 2,26" fill="var(--blue)"/><circle cx="44" cy="48" r="18" fill="none" stroke="#fff" stroke-width="3"/><polyline points="35,48 42,55 54,40" fill="none" stroke="#fff" stroke-width="3"/></svg>
      <p>Integrate aesthetic control into a total quality management (TQM) approach with precise indicators at all stages</p>
    </div>
    <div class="feature">
      <svg width="88" height="96" viewBox="0 0 88 96"><polygon points="44,2 86,26 86,70 44,94 2,70 2,26" fill="var(--blue)"/><line x1="30" y1="64" x2="56" y2="34" stroke="#fff" stroke-width="5" stroke-linecap="round"/><circle cx="58" cy="32" r="7" fill="none" stroke="#fff" stroke-width="3"/></svg>
      <p>Provide the after-sales service with an efficient tool to record the aesthetic aspect of the supported product</p>
    </div>
  </div>
</section>

<!-- semantic matrix -->
<section class="section" style="top:3640px;height:310px;background:var(--grey-bg)">
  <h2 class="heading" style="margin-top:80px">A semantic matrix of<br>aesthetic defects</h2>
  <div class="marker"></div>
  <p style="position:absolute;top:222px;left:150px;width:900px;text-align:center;font-size:13.5px;line-height:26px">KFS is based on a semantic matrix that defines 5 levels of intensity for each of the 5 types of aesthetic defects referenced:<br>Scratches -Marks - Deformations - Stains - Uniformity.</p>
</section>

<!-- total quality band -->
<section class="section" style="top:3950px;height:690px">
  <svg class="band-bg" width="1200" height="690" viewBox="0 0 1200 690">
    <defs><linearGradient id="g3" x1="0" y1="0" x2="1" y2="1"><stop offset="0" stop-color="#0a72c4"/><stop offset="1" stop-color="#0b5fae"/></linearGradient></defs>
    <rect width="1200" height="690" fill="url(#g3)"/>
    <polygon points="0,0 1200,130 0,130" fill="var(--navy)"/>
    <polygon points="0,0 1200,0 1200,130" fill="var(--grey-bg)"/>
    <polygon points="0,610 1200,560 1200,690 0,690" fill="var(--navy)"/>
  </svg>
  <div role="img" aria-label="Decorative flowing dot wave" style="position:absolute;left:0;top:380px;width:1200px;height:220px;background:radial-gradient(ellipse at 50% 60%,rgba(140,200,255,.3),transparent 60%)"></div>
  <h2 class="heading light" style="position:absolute;top:188px;width:1200px">Improving the total quality<br>approach</h2>
  <div class="marker light" style="position:absolute;top:283px;left:588px;margin:0"></div>
  <div class="photo" style="left:112px;top:305px;width:468px;height:227px;background:radial-gradient(ellipse at 45% 55%,#8a7a5a 0%,#3b352c 45%,#161616 90%)" role="img" aria-label="Watchmaker's gloved hands holding a watch movement with tweezers"></div>
  <p class="body-copy" style="left:613px;top:310px;width:477px;color:var(--white)">During the entire product life cycle, from design through customer service to distribution, the KFS application makes it possible to build up a database of aesthetic defects in a simple, efficient and computerised way.</p>
  <p class="body-copy" style="left:613px;top:413px;width:477px;color:var(--white)">On this basis of consolidated data, it is then possible to establish recurrences, such as potential correlations, thus enabling solutions to be found to correct, improve and optimise the product, process or service offert.</p>
</section>

<!-- footer -->
<footer class="section footer">
  <div class="fcol" style="left:112px;width:232px">
    <div class="brand-f">Kestrel Finish<br>Studio</div>
    <p style="margin-top:14px;text-align:justify">Lorem ipsum dolor sit amet, consecte tur adipiscing elit, sed do eiusmod tempor incididunt ut labore et dolore magna aliqua. Ut enim ad minim veniam,quis nostrud</p>
  </div>
  <div class="fcol" style="left:459px;width:230px">
    <h4>Contact us</h4>
    <div class="contact-row"><svg width="26" height="26" viewBox="0 0 26 26"><circle cx="13" cy="13" r="13" fill="var(--ink)"/><circle cx="13" cy="11" r="4" fill="#fff"/><polygon points="9,13 17,13 13,19" fill="#fff"/></svg><p>123, Lorem ipsum dolor sit<br>consectetur adipiscing</p></div>
    <div class="contact-row"><svg width="26" height="26" viewBox="0 0 26 26"><circle cx="13" cy="13" r="13" fill="var(--ink)"/><path d="M9 8 l3 0 l1 4 l-2 1 q1 3 4 4 l1-2 l4 1 l0 3 q-9 0 -11 -11z" fill="#fff"/></svg><p>Call Us<br>+41 79 210 58 63</p></div>
    <div class="contact-row"><svg width="26" height="26" viewBox="0 0 26 26"><circle cx="13" cy="13" r="13" fill="var(--ink)"/><rect x="7" y="9" width="12" height="8" fill="#fff"/><polyline points="7,9 13,14 19,9" fill="none" stroke="var(--ink)" stroke-width="1.2"/></svg><p>E mail Us<br>info@kestrelfinish.ch</p></div>
  </div>
  <div class="fcol links" style="left:767px">
    <h4 style="margin-bottom:14px">Menu</h4>
    <a>Home</a><a>About Us</a><a>Services</a><a>Reviews</a><a>Contact Us</a>
  </div>
  <div class="fcol links" style="left:937px">
    <h4 style="margin-bottom:14px">Support</h4>
    <a>Privacy policy</a><a>Terms &amp; Condition</a><a>Faq</a><a>Contact us</a><a>Support</a>
  </div>
</footer>
<div class="divider"></div>
<div class="copyright">Copyright © 2023 All Rights Reserved</div>

</body>
</html>
```